Indy Film Production Company/Studio

We need a business card designed from an existing logo. We are a digital studio/production company that caters to creating genre entertainment, like Action, Horror, and martial arts. The card along with the logo will be used to Brand the company from letter heads to banners. The design will also be used for postcards and Brochures. It should be professional and masculine.
Updates

Thank you to all the designers who have participated. I'm narrowing down who it will be. Thank you again.

Target Market(s)

Investors, Networks, Producers, and actors

Industry/Entity Type

Film Production

Contact Information for Business Card

Teodoro Valbuena
Producer/Writer/Director
www.kestrelpicturehouse.example

Requirements
Must have
• Website address, Facebook icon and Twitter icon possibly in the back of the card.
Nice to have
• Logline of Company: Follow The Action.

```html
<!DOCTYPE html>
<html lang="en">
<head>
<meta charset="utf-8">
<title>Kestrel Picture House – Business Card</title>
<link rel="stylesheet" href="https://fonts.googleapis.com/css2?family=Open+Sans:wght@400;600;800&display=swap">
<style>
  :root {
    --stage: #ebe7e3;
    --brand-red: #e8262b;
    --brand-red-deep: #d41f24;
    --paper-white: #f7f6f4;
    --ink-white: #ffffff;
  }
  * { box-sizing: border-box; margin: 0; padding: 0; }
  html, body {
    width: 1200px; height: 900px; overflow: hidden;
    background: var(--stage);
    font-family: "Open Sans", Arial, sans-serif;
  }
  .canvas { position: relative; width: 1200px; height: 900px; }

  .card {
    position: absolute;
    box-shadow: 0 6px 18px rgba(0,0,0,0.18);
  }
  .card--front {
    left: 238px; top: 62px; width: 555px; height: 343px;
    background: var(--brand-red);
    color: var(--ink-white);
  }
  .card--back {
    left: 457px; top: 518px; width: 560px; height: 344px;
    background: var(--paper-white);
  }

  .holder { position: absolute; left: 33px; top: 65px; }
  .holder__name { font-size: 20px; font-weight: 600; line-height: 1.2; }
  .holder__role { font-size: 14px; font-weight: 400; margin-top: 2px; }

  .contact { position: absolute; left: 33px; top: 167px; font-size: 14px; line-height: 20px; }
  .contact__address { margin-bottom: 8px; }
  .contact__row { display: flex; align-items: center; gap: 8px; }
  .contact__icon { width: 14px; height: 14px; flex: none; fill: var(--ink-white); }

  .wordmark {
    position: absolute;
    font-weight: 800;
    text-transform: uppercase;
    text-align: center;
    line-height: 1.05;
  }
  .wordmark--embossed {
    left: 280px; top: 120px; width: 240px;
    font-size: 29px;
    color: var(--brand-red-deep);
  }
  .wordmark--primary {
    left: 145px; top: 108px; width: 290px;
    font-size: 38px;
    color: var(--brand-red);
  }
</style>
</head>
<body>
<main class="canvas">
  <section class="card card--front" aria-label="Business card front">
    <div class="holder">
      <p class="holder__name">Teodoro Valbuena</p>
      <p class="holder__role">Producer/Writer/Director</p>
    </div>
    <div class="contact">
      <p class="contact__address">12345, Address Goes Here<br>Country Name, 123456.</p>
      <p class="contact__row">
        <svg class="contact__icon" viewBox="0 0 24 24" aria-hidden="true"><path d="M6.6 10.8a15.1 15.1 0 0 0 6.6 6.6l2.2-2.2a1 1 0 0 1 1-.25 11.4 11.4 0 0 0 3.6.57 1 1 0 0 1 1 1V20a1 1 0 0 1-1 1A17 17 0 0 1 3 4a1 1 0 0 1 1-1h3.5a1 1 0 0 1 1 1c0 1.25.2 2.45.57 3.57a1 1 0 0 1-.25 1z"/></svg>
        044-555 010 274
      </p>
      <p class="contact__row">
        <svg class="contact__icon" viewBox="0 0 24 24" aria-hidden="true"><path d="M3 6h18v12H3z M3 6l9 7 9-7" fill="none" stroke="#fff" stroke-width="2"/></svg>
        info@kestrelpicturehouse.example
      </p>
      <p class="contact__row">
        <svg class="contact__icon" viewBox="0 0 24 24" aria-hidden="true"><circle cx="12" cy="12" r="9" fill="none" stroke="#fff" stroke-width="2"/><path d="M3 12h18M12 3c3 3.5 3 14.5 0 18M12 3c-3 3.5-3 14.5 0 18" fill="none" stroke="#fff" stroke-width="1.6"/></svg>
        www.kestrelpicturehouse.example
      </p>
    </div>
    <p class="wordmark wordmark--embossed">Kestrel Picture House</p>
  </section>

  <section class="card card--back" aria-label="Business card back">
    <p class="wordmark wordmark--primary">Kestrel Picture House</p>
  </section>
</main>
</body>
</html>
```